Infoblatt
Zielgruppe
Talentförderung, Personalentwicklung, Beratung von Personalabteilungen
Zielgruppe: Personaler, HR Verantwortliche
Aufgabenstellung
Es geht um einen "One-Pager", der auf einem Kongress ausgelegt werden soll und in Kurzform einen Überblick über unser Unternehmen und unser Angebot informieren soll.
Wir haben Visitenkarten auf Recyclingpapier und möchten das Blatt konsistent auf das gleiche Papier drucken lassen, daher einfarbig schwarz. Format DIN A4 Hoch.
IDEE: Vom Stil wie eine Infografik aufbauen
TYPO: unser LOGO ist BEBAS NEUE und unsere Schrift Helvetica

```html
<!DOCTYPE html>
<html lang="de">
<head>
<meta charset="utf-8">
<title>Infoblatt – Credo, Mehrwert, Mission</title>
<link rel="stylesheet" href="https://fonts.googleapis.com/css2?family=Oswald:wght@600;700&family=Arimo:wght@400;700&display=swap">
<style>
  :root{
    --ink:#111111;
    --paper:#ffffff;
    --grey-dark:#4a4a4a;
    --grey-mid:#9a9a9a;
    --grey-light:#d9d9d9;
  }
  *{margin:0;padding:0;box-sizing:border-box}
  html,body{width:849px;height:1200px;overflow:hidden;background:var(--paper)}
  .sheet{position:relative;width:849px;height:1200px;overflow:hidden;background:var(--paper);color:var(--ink);font-family:"Arimo",Helvetica,Arial,sans-serif}
  .backdrop{position:absolute;inset:0;
    background:
      radial-gradient(ellipse 260px 200px at 150px 80px, var(--grey-dark) 0%, #777 45%, transparent 75%),
      radial-gradient(ellipse 380px 300px at 600px 560px, #b4b4b4 0%, #d4d4d4 50%, transparent 80%),
      linear-gradient(180deg, #bdbdbd 0%, #d6d6d6 30%, #e4e4e4 55%, #ededed 75%, #f6f6f6 100%);}
  .facets{position:absolute;inset:0}
  .block{position:absolute}
  .title{font-family:"Oswald","Bebas Neue",sans-serif;font-weight:700;font-size:44px;line-height:1;letter-spacing:.5px;text-transform:uppercase}
  .subtitle{font-family:"Oswald",sans-serif;font-weight:600;font-size:29px;line-height:1.1;margin-top:8px}
  .copy{font-size:15.5px;font-weight:700;line-height:31px}
  .credo{right:52px;top:112px;text-align:right}
  .credo .copy{margin-top:34px}
  .mehrwert{left:194px;top:440px;width:560px}
  .mehrwert .copy{margin-top:24px;font-size:15.5px;line-height:29px}
  .offer{margin-top:24px;font-size:15.5px;line-height:25px}
  .offer h3{font-size:15.5px;font-weight:700}
  .offer ul{list-style:none}
  .offer li{font-weight:400}
  .offer li::before{content:"- "}
  .mission{left:194px;top:895px;width:560px}
  .mission .copy{margin-top:26px;font-size:14.5px;line-height:25px}
</style>
</head>
<body>
<main class="sheet">
  <div class="backdrop" role="img" aria-label="Schwarzweiß-Foto: Dartscheibe oben links, darunter unscharfer Schreibtisch mit Unterlagen"></div>
  <svg class="facets" width="849" height="1200" viewBox="0 0 849 1200" aria-hidden="true">
    <polygon points="300,0 849,0 849,380 460,400" fill="#ffffff" opacity=".55"/>
    <polygon points="380,0 849,0 849,250" fill="#ffffff" opacity=".5"/>
    <polygon points="0,380 0,0 300,0" fill="#ffffff" opacity=".18"/>
    <polygon points="180,420 700,560 560,780 180,780" fill="#ffffff" opacity=".55"/>
    <polygon points="180,420 849,470 849,790 560,780" fill="#ffffff" opacity=".35"/>
    <polygon points="0,420 180,420 180,1200 0,1200" fill="#ffffff" opacity=".25"/>
    <polygon points="0,780 849,790 849,1200 0,1200" fill="#ffffff" opacity=".5"/>
    <polygon points="180,860 849,820 849,1200 180,1200" fill="#ffffff" opacity=".45"/>
  </svg>

  <section class="block credo">
    <h2 class="title">Credo</h2>
    <p class="subtitle">Woran wir glauben</p>
    <p class="copy">Wir glauben, dass sich persönliche und ökonomische<br>Werte ergänzen - mehr noch, dass sie langfristig nicht<br>ohne einander auskommen und dass sich emotionale<br>Bindung als Mehrwert in Zahlen ausdrückt.</p>
  </section>

  <section class="block mehrwert">
    <h2 class="title">Mehrwert</h2>
    <p class="subtitle">Was wir bieten</p>
    <p class="copy">Wir beraten Unternehmen im Rahmen der Talentförderung<br>und helfen Jugendlichen auf dem Weg in ihr Berufsleben.</p>
    <div class="offer">
      <h3>Für Unternehmen:</h3>
      <ul>
        <li>Talentförderung &amp; Talent Management</li>
        <li>Professionalisierung der Personalarbeit</li>
        <li>Organisationsentwicklung</li>
        <li>Potentialorientierte Mitarbeiterführung</li>
      </ul>
    </div>
    <div class="offer">
      <h3>Für die junge Generation:</h3>
      <ul>
        <li>Berufsorientierung</li>
        <li>Bewerbungscoaching</li>
      </ul>
    </div>
  </section>

  <section class="block mission">
    <h2 class="title">Mission</h2>
    <p class="subtitle">Was unser Handeln leitet:</p>
    <p class="copy">Kundare heißt marktschreierisch anpreisen, hinters Licht führen, täuschen.<br>Mandare heißt beauftragen, Vertrauen schenken. Wir legen großen Wert<br>auf eine Beziehung, die Mandare, nicht Kundare entspricht. Für uns ist der<br>partnerschaftliche Umgang mit unseren Mandanten das Fundament. Wir<br>haben keine Kunden. Wir unterstützen Mandanten.</p>
  </section>
</main>
</body>
</html>
```